Tall Fern Roofing Business Card

Need a business card with the logo that was designed here

Contact Information for Business Card

Name, Title, Phone, Email, Website, Company name

```html
<!DOCTYPE html>
<html lang="en">
<head>
<meta charset="utf-8">
<title>Tall Fern Roofing Business Card</title>
<link href="https://fonts.googleapis.com/css2?family=Montserrat:wght@700&family=Open+Sans:wght@400;600&display=swap" rel="stylesheet">
<style>
  :root {
    --page: #242424;
    --card-dark: #222226;
    --brand-blue: #1474c4;
    --blue-light: #2a8ad8;
    --blue-deep: #0f62a8;
    --grey: #97999d;
    --white: #ffffff;
  }
  * { margin: 0; padding: 0; box-sizing: border-box; }
  html, body { width: 1200px; height: 780px; overflow: hidden; background: var(--page); }
  .canvas { position: relative; width: 1200px; height: 780px; }

  .card {
    position: absolute;
    width: 600px;
    height: 343px;
    overflow: hidden;
    box-shadow: 0 14px 30px rgba(0,0,0,0.55);
  }

  /* Back side */
  .card-back { left: 80px; top: 40px; }
  .back-pattern {
    position: absolute; inset: 0;
    background: linear-gradient(160deg, var(--blue-light) 0%, var(--brand-blue) 55%, var(--blue-deep) 100%);
  }
  .back-brand {
    position: absolute; right: 60px; bottom: 70px;
    font-family: "Open Sans", sans-serif; font-weight: 600;
    font-size: 22px; color: var(--white);
  }

  /* Front side */
  .card-front { left: 520px; top: 397px; background: var(--card-dark); }
  .front-brand {
    position: absolute; left: 40px; top: 46px;
    font-family: "Open Sans", sans-serif; font-weight: 600;
    font-size: 26px; color: var(--brand-blue);
  }
  .brand-rule {
    position: absolute; left: 40px; top: 100px; width: 250px; height: 1px;
    background: var(--brand-blue);
  }
  .person { position: absolute; right: 40px; top: 34px; text-align: right; }
  .person-name {
    font-family: "Montserrat", sans-serif; font-weight: 700;
    font-size: 32px; line-height: 1.1;
  }
  .person-name .first { color: var(--brand-blue); }
  .person-name .last { color: var(--grey); }
  .person-title {
    font-family: "Open Sans", sans-serif; font-weight: 600;
    font-size: 14px; color: var(--white); margin-top: 2px;
    padding-bottom: 4px; border-bottom: 1px solid var(--white);
  }
  .name-bar {
    position: absolute; right: 0; top: 36px; width: 18px; height: 48px;
    background: var(--brand-blue);
  }
  .divider {
    position: absolute; left: 40px; top: 128px; width: 520px; height: 1px;
    background: var(--white);
  }
  .address {
    position: absolute; left: 40px; top: 148px;
    font-family: "Open Sans", sans-serif; font-size: 15px; line-height: 1.35;
    color: var(--white);
  }
  .contact-list {
    position: absolute; left: 40px; top: 210px; list-style: none;
    font-family: "Open Sans", sans-serif; font-size: 15px; line-height: 1.45;
    color: var(--white);
  }
  .contact-list li { display: flex; align-items: center; gap: 10px; }
  .contact-icon { width: 14px; height: 14px; flex: none; }
  .swoosh { position: absolute; left: 0; bottom: 0; width: 600px; height: 343px; }
</style>
</head>
<body>
<main class="canvas">

  <section class="card card-back" aria-label="Card back">
    <div class="back-pattern" role="img" aria-label="Repeating pattern of small house rooflines in blue tones"></div>
    <p class="back-brand">Tall Fern Roofing</p>
  </section>

  <section class="card card-front" aria-label="Card front">
    <svg class="swoosh" viewBox="0 0 600 343" aria-hidden="true">
      <path d="M170 343 C 300 250, 430 190, 600 168 L 600 343 Z" fill="var(--brand-blue)"/>
      <path d="M290 343 C 380 260, 470 210, 600 190 L 600 343 Z" fill="var(--card-dark)"/>
      <path d="M300 343 C 390 266, 480 218, 600 196 L 600 343 Z" fill="var(--grey)"/>
    </svg>

    <p class="front-brand">Tall Fern Roofing</p>
    <div class="brand-rule"></div>

    <div class="person">
      <p class="person-name"><span class="first">Owen</span> <span class="last">Marsh</span></p>
      <p class="person-title">Managing Director</p>
    </div>
    <div class="name-bar"></div>

    <div class="divider"></div>

    <p class="address">418 Cedar Ridge Rd. Suite 120<br>Maple Falls, TX 76540</p>

    <ul class="contact-list">
      <li>
        <svg class="contact-icon" viewBox="0 0 16 16" aria-hidden="true"><path d="M3 1.5l3 3-1.6 1.8a9 9 0 0 0 5.3 5.3L11.5 10l3 3-2 2C6.5 14.5 1.5 9.5 1 3.5z" fill="var(--brand-blue)"/></svg>
        <span>(555) 214-3870</span>
      </li>
      <li>
        <svg class="contact-icon" viewBox="0 0 16 16" aria-hidden="true"><rect x="1" y="3" width="14" height="10" fill="var(--brand-blue)"/><path d="M1 3l7 5.5L15 3" stroke="var(--card-dark)" stroke-width="1.3" fill="none"/></svg>
        <span>info@website.com</span>
      </li>
      <li>
        <svg class="contact-icon" viewBox="0 0 16 16" aria-hidden="true"><circle cx="8" cy="8" r="7" fill="var(--brand-blue)"/><path d="M1 8h14M8 1c-3 3.5-3 10.5 0 14M8 1c3 3.5 3 10.5 0 14" stroke="var(--card-dark)" stroke-width="1" fill="none"/></svg>
        <span>www.website.com</span>
      </li>
    </ul>
  </section>

</main>
</body>
</html>
```